Building Design company needing a letterhead

We need a letter head for our Building Design company to send letters etc. to our clients, consultants, councils etc. We would like to see our logo used and company colours. I have attached our style guide and an example of our current letterheads. Top left we would like our logo, top right we would like the company details and at the footer we would like some sort of image/design etc. that suits our brand. I like the Tarrow Design letterhead attached.

Target Market(s)

Professionals, Councils, Consultants, Mums & Dads

Industry/Entity Type

Architecture

Other font styles liked:
• refer the design style guide

Colors
f37122
000000
1b1b1b

Requirements
Must have
• Must have the minimum of a logo, company details and footer
Nice to have
• An image/design made for the footer that would suite our brand and website at www.corvanplans.com.au. Also it would be nice to include the KMEOT logo somewhere perhaps included in the footer.
Should not have
• Large images in the header. I just want the logo and company details.

```html
<!DOCTYPE html>
<html lang="en">
<head>
<meta charset="utf-8">
<title>Halvern Design Letterhead</title>
<link href="https://fonts.googleapis.com/css2?family=Titillium+Web:wght@600&family=Questrial&family=Open+Sans:wght@400&display=swap" rel="stylesheet">
<style>
  :root {
    --backdrop: #161616;
    --paper: #ffffff;
    --ink: #1b1b1b;
    --brand: #f37122;
    --brand-deep: #e65f2b;
    --brand-soft: #ed8049;
    --rule: #e2e2e2;
    --ghost: #ececec;
  }
  * { margin: 0; padding: 0; box-sizing: border-box; }
  html, body { width: 960px; height: 1200px; overflow: hidden; background: var(--backdrop); }
  .letterhead {
    position: absolute; left: 178px; top: 122px;
    width: 632px; height: 945px;
    background: var(--paper); overflow: hidden;
  }
  .brand {
    position: absolute; left: 34px; top: 34px;
    display: flex; align-items: center; gap: 12px;
  }
  .brand-mark { width: 26px; height: 26px; background: var(--brand); }
  .brand-name {
    font-family: "Titillium Web", sans-serif; font-weight: 600;
    font-size: 23px; line-height: 23px; letter-spacing: 1px;
    color: var(--ink); text-transform: uppercase;
  }
  .header-rule { position: absolute; left: 0; right: 0; top: 98px; height: 1px; background: var(--rule); }
  .contact {
    position: absolute; right: 42px; top: 18px; text-align: right;
    font-family: "Questrial", sans-serif; font-variant: small-caps;
    letter-spacing: 1.2px; color: var(--ink);
  }
  .contact-name { color: var(--brand); font-size: 12px; line-height: 14px; }
  .contact-role { font-size: 10px; line-height: 12px; margin-bottom: 8px; }
  .contact-line { font-size: 10px; line-height: 15px; display: flex; justify-content: flex-end; align-items: center; gap: 6px; }
  .contact-line svg { width: 8px; height: 8px; fill: var(--brand); }
  .watermark {
    position: absolute; left: 60px; top: 500px;
    transform: rotate(-28deg); transform-origin: left top;
    font-family: "Titillium Web", sans-serif; font-weight: 600;
    font-size: 82px; line-height: 80px; color: var(--ghost);
    text-transform: uppercase; letter-spacing: 4px; white-space: nowrap;
  }
  .footer-wave { position: absolute; left: 0; top: 0; }
  .footer-address {
    position: absolute; left: 34px; top: 910px;
    font-family: "Open Sans", sans-serif; font-size: 9px; color: var(--paper);
  }
  .footer-contact {
    position: absolute; right: 45px; top: 870px; text-align: right;
    font-family: "Open Sans", sans-serif; font-size: 9px; line-height: 13.4px; color: var(--paper);
  }
  .footer-contact div { display: flex; justify-content: flex-end; align-items: center; gap: 6px; }
  .footer-contact svg { width: 8px; height: 8px; fill: var(--paper); }
</style>
</head>
<body>
<main class="letterhead">
  <div class="watermark" aria-hidden="true">Halvern<br>Design</div>

  <header>
    <div class="brand">
      <span class="brand-mark"></span>
      <div class="brand-name">Halvern<br>Design</div>
    </div>
    <div class="contact">
      <div class="contact-name">Alex Reed</div>
      <div class="contact-role">Deisgnation</div>
      <div class="contact-line">(123) 456-7890
        <svg viewBox="0 0 10 10"><path d="M2 0h2l1 3-1.5 1a6 6 0 0 0 2.5 2.5L7 5l3 1v2c0 1-1 2-2 2A8 8 0 0 1 0 2c0-1 1-2 2-2z"/></svg></div>
      <div class="contact-line">info@companyname.com
        <svg viewBox="0 0 10 10"><path d="M0 2h10v6H0z M0 2l5 3.5L10 2" stroke="#fff" stroke-width=".8"/></svg></div>
      <div class="contact-line">companyname.com
        <svg viewBox="0 0 10 10"><circle cx="5" cy="5" r="4.3" fill="none" stroke="var(--brand)" stroke-width=".9"/><path d="M1 5h8M5 .7v8.6" stroke="var(--brand)" stroke-width=".7"/></svg></div>
    </div>
    <div class="header-rule"></div>
  </header>

  <svg class="footer-wave" width="632" height="945" viewBox="0 0 632 945" aria-hidden="true">
    <defs>
      <linearGradient id="footerFill" x1="1" y1="0" x2="0.2" y2="1">
        <stop offset="0" stop-color="var(--brand-deep)"/>
        <stop offset="1" stop-color="var(--brand-soft)"/>
      </linearGradient>
    </defs>
    <path d="M0 882 C 220 894, 480 872, 632 788 L632 945 L0 945 Z" fill="url(#footerFill)"/>
  </svg>

  <footer>
    <div class="footer-address">Address Line1, Addres Line2 Country -123456</div>
    <div class="footer-contact">
      <div>123-456-7890 <svg viewBox="0 0 10 10"><path d="M0 4c2-3 8-3 10 0v1H7V4H3v1H0z M2 6h6l1 3H1z"/></svg></div>
      <div>123-456-7890 <svg viewBox="0 0 10 10"><path d="M2 0h6v3h2v7H0V3h2z M3 1v2h4V1z"/></svg></div>
      <div>info@companyname.com <svg viewBox="0 0 10 10"><path d="M0 2h10v6H0z"/></svg></div>
      <div>www.companyname.com <svg viewBox="0 0 10 10"><path d="M6 1l3 3-2 2-1-1 1-1-1-1-3 3 1 1-1 1-2-2z" fill="none" stroke="#fff" stroke-width="1"/></svg></div>
    </div>
  </footer>
</main>
</body>
</html>
```